Local Roofing/Construction company business needs new biz card design

We need a new business card design, current cards are from the start of this operation and generic at best. We are a local Construction Company (General Contractor) with a majority of our work originating from insurance claims-exterior finish work is the main focus (Roofs-Siding-Gutters etc). Heavily involved with homeowners and the low ball offers they receive from insurance company's after a insurable event takes place. I have attached some of our original logo file(s) below.

```html
<!DOCTYPE html>
<html lang="en">
<head>
<meta charset="utf-8">
<title>Stonefield Construction – Business Card</title>
<link rel="stylesheet" href="https://fonts.googleapis.com/css2?family=Open+Sans:wght@400;600;700;800&display=swap">
<style>
  :root {
    --stage: #222222;
    --paper: #f4f4f4;
    --green: #4cb86a;
    --ink: #0e1f22;
    --text: #1a1a1a;
    --rule: #333333;
    --white: #ffffff;
  }
  * { box-sizing: border-box; margin: 0; padding: 0; }
  html, body {
    width: 1200px; height: 780px; overflow: hidden;
    background: var(--stage);
    font-family: "Open Sans", sans-serif;
  }
  .stage { position: relative; width: 1200px; height: 780px; }

  .card {
    position: absolute; top: 240px;
    width: 525px; height: 300px;
    overflow: hidden;
    box-shadow: 0 14px 30px rgba(0,0,0,.45);
  }

  /* Front */
  .card-front { left: 50px; background: var(--paper); }
  .brand-box {
    position: absolute; left: 30px; top: 40px;
    width: 225px; height: 88px;
    background: var(--ink);
    border-radius: 12px;
    display: flex; align-items: center; justify-content: center; gap: 12px;
  }
  .brand-box .mark-square { width: 18px; height: 18px; background: var(--green); flex: none; }
  .brand-name {
    color: var(--white); font-weight: 800; font-size: 18px;
    letter-spacing: .4px; line-height: 1.1; text-transform: uppercase;
  }
  .divider { position: absolute; left: 0; top: 0; width: 525px; height: 300px; }
  .contact { position: absolute; left: 288px; top: 92px; width: 200px; }
  .person-name { font-size: 23px; font-weight: 800; color: var(--ink); line-height: 1.05; white-space: nowrap; }
  .person-name .first { color: var(--green); }
  .person-role { font-size: 12px; font-weight: 600; color: var(--text); margin: 3px 0 9px; }
  .contact-list { list-style: none; }
  .contact-list li {
    display: flex; align-items: center; gap: 7px;
    font-size: 12px; color: var(--text); line-height: 18px; white-space: nowrap;
  }
  .contact-list svg { width: 11px; height: 11px; flex: none; }
  .address-band {
    position: absolute; left: 0; bottom: 30px;
    width: 438px; height: 28px; background: var(--green);
    color: var(--white); font-size: 13px; line-height: 28px; padding-left: 22px;
  }
  .corner-block {
    position: absolute; right: 0; bottom: 0;
    width: 82px; height: 58px; background: var(--ink);
    clip-path: polygon(32% 0, 100% 0, 100% 100%, 0 100%);
  }

  /* Back */
  .card-back { left: 625px; background: var(--green); }
  .pattern-fill {
    position: absolute; inset: 0;
    background: linear-gradient(135deg, var(--green) 0%, #43b062 100%);
  }
  .back-brand {
    position: absolute; right: 26px; bottom: 24px;
    display: flex; align-items: center; gap: 7px;
    color: var(--white); font-weight: 800; font-size: 12px; text-transform: uppercase;
  }
  .back-brand .mark-square { width: 12px; height: 12px; border: 2px solid var(--white); }
</style>
</head>
<body>
<main class="stage">

  <section class="card card-front" aria-label="Business card front">
    <div class="brand-box">
      <span class="mark-square"></span>
      <span class="brand-name">Stonefield<br>Construction</span>
    </div>

    <svg class="divider" viewBox="0 0 525 300" aria-hidden="true">
      <line x1="282" y1="88" x2="226" y2="222" stroke="#333" stroke-width="0.8"/>
    </svg>

    <div class="contact">
      <p class="person-name"><span class="first">Marta</span> Halloway</p>
      <p class="person-role">Co-Founder</p>
      <ul class="contact-list">
        <li><svg viewBox="0 0 12 12"><path fill="#4cb86a" d="M3 1l2 2-1 1.5c.6 1.4 1.6 2.4 3 3L8.5 6.5l2 2L9 10.5C5 10 2 7 1.5 3z"/></svg>555-214-0187</li>
        <li><svg viewBox="0 0 12 12"><path fill="#4cb86a" d="M3 1l2 2-1 1.5c.6 1.4 1.6 2.4 3 3L8.5 6.5l2 2L9 10.5C5 10 2 7 1.5 3z"/></svg>555-309-4426 (Emergency)</li>
        <li><svg viewBox="0 0 12 12"><circle cx="6" cy="6" r="5" fill="none" stroke="#4cb86a" stroke-width="1.4"/><path d="M1 6h10M6 1c-2.5 3-2.5 7 0 10M6 1c2.5 3 2.5 7 0 10" fill="none" stroke="#4cb86a" stroke-width="1"/></svg>www.stonefieldbuild.com</li>
        <li><svg viewBox="0 0 12 12"><rect x="1" y="2.5" width="10" height="7" rx="1" fill="#4cb86a"/><path d="M1.5 3l4.5 3.5L10.5 3" fill="none" stroke="#fff" stroke-width="1"/></svg>hello@stonefieldbuild.com</li>
      </ul>
    </div>

    <div class="address-band">42 Orchard Ridge Ln, Fairhaven, MO 63000</div>
    <div class="corner-block"></div>
  </section>

  <section class="card card-back" aria-label="Business card back">
    <div class="pattern-fill" role="img" aria-label="Repeating tonal green brand pattern covering the card"></div>
    <div class="back-brand"><span class="mark-square"></span>Stonefield</div>
  </section>

</main>
</body>
</html>
```